Harbor Loom Floors Letterhead

Letterhead used for business reasons. It must be editable and easy to use.

Address is 2715 W. Pelican Lane Marlow Bay SC 34187 - 728.382.6519

```html
<!DOCTYPE html>
<html lang="en">
<head>
<meta charset="utf-8">
<title>Harbor Loom Floors Letterhead</title>
<link rel="stylesheet" href="https://fonts.googleapis.com/css2?family=Lato:wght@400;700&family=Montserrat:wght@400;500&display=swap">
<style>
  :root {
    --accent: #e0962a;
    --ink: #1c1c1c;
    --muted: #555555;
    --paper: #ffffff;
    --backdrop: #ececec;
  }
  * { margin: 0; padding: 0; box-sizing: border-box; }
  html, body { width: 1200px; height: 1200px; overflow: hidden; background: var(--backdrop); }
  body { display: flex; align-items: center; justify-content: center; }

  .letterhead {
    position: relative;
    width: 860px;
    height: 1112px;
    background: var(--paper);
    box-shadow: 0 2px 12px rgba(0,0,0,0.12);
    font-family: "Lato", Arial, sans-serif;
    color: var(--ink);
  }

  .brand {
    position: absolute;
    left: 64px;
    top: 118px;
    display: flex;
    align-items: center;
    gap: 12px;
  }
  .brand-dot { width: 18px; height: 18px; border-radius: 50%; background: var(--accent); }
  .brand-name {
    font-family: "Lato", Arial, sans-serif;
    font-weight: 700;
    font-size: 30px;
    letter-spacing: 0.5px;
    color: var(--accent);
  }

  .header-rule { position: absolute; left: 64px; right: 0; top: 172px; height: 1.5px; background: var(--accent); }
  .contact-divider { position: absolute; left: 560px; top: 112px; width: 1.5px; height: 60px; background: var(--accent); }

  .contact {
    position: absolute;
    left: 584px;
    top: 92px;
    font-family: "Montserrat", Arial, sans-serif;
    font-style: normal;
    font-size: 12.5px;
    line-height: 17px;
    color: var(--muted);
  }
  .contact-phone { display: flex; align-items: center; gap: 6px; margin-top: 4px; }
  .contact-phone svg { width: 11px; height: 11px; }

  .letter-body {
    position: absolute;
    left: 96px;
    right: 80px;
    top: 224px;
    font-size: 14.5px;
    line-height: 19px;
  }
  .date { margin-bottom: 20px; }
  .recipient { margin-bottom: 22px; }
  .recipient-company { margin-bottom: 26px; }
  .salutation { font-weight: 700; font-size: 18px; margin-bottom: 30px; }
  .paragraph { margin-bottom: 19px; }
  .closing { margin-top: 40px; }
</style>
</head>
<body>
  <main class="letterhead">
    <div class="brand">
      <span class="brand-dot"></span>
      <span class="brand-name">Harbor Loom Floors</span>
    </div>

    <div class="contact-divider"></div>
    <address class="contact">
      <div>2715 W. Pelican Lane</div>
      <div>Marlow Bay SC 34187</div>
      <div class="contact-phone">
        <svg viewBox="0 0 24 24" aria-hidden="true"><path fill="#e0962a" d="M6.6 10.8a15.1 15.1 0 0 0 6.6 6.6l2.2-2.2a1 1 0 0 1 1-.25 11.4 11.4 0 0 0 3.6.57 1 1 0 0 1 1 1V20a1 1 0 0 1-1 1A17 17 0 0 1 3 4a1 1 0 0 1 1-1h3.5a1 1 0 0 1 1 1c0 1.25.2 2.45.57 3.57a1 1 0 0 1-.25 1z"/></svg>
        <span>728.382.6519</span>
      </div>
    </address>

    <div class="header-rule"></div>

    <section class="letter-body">
      <p class="date">January-03-2020</p>
      <div class="recipient">
        <p>Mr, John Doe</p>
        <p>President</p>
      </div>
      <div class="recipient-company">
        <p>Brightwell Corporation</p>
        <p>123 Street Name, Suite# 10</p>
        <p>City, State, 120023</p>
      </div>
      <p class="salutation">Dear Mr, John</p>
      <p class="paragraph">Lorem ipsum dolor sit amet, consectetur adipiscing elit, sed do eiusmod tempor incididunt ut labore et dolore magna aliqua. Ut enim ad minim veniam, quis nostrud exercitation ullamco laboris nisi ut aliquip ex ea commodo consequat. Duis aute irure dolor in reprehenderit in voluptate velit esse cillum dolore eu fugiat nulla pariatur.</p>
      <p class="paragraph">Lorem ipsum dolor sit amet, consectetur adipiscing elit, sed do eiusmod tempor incididunt ut labore et dolore magna aliqua. Ut enim ad minim veniam, quis nostrud exercitation ullamco laboris nisi ut aliquip ex ea commodo consequat. Duis aute irure dolor in reprehenderit in voluptate velit esse cillum dolore eu fugiat nulla pariatur.</p>
      <p class="paragraph">Lorem ipsum dolor sit amet, consectetur adipiscing elit, sed do eiusmod tempor incididunt ut labore et dolore magna aliqua. Ut enim ad minim veniam, quis nostrud exercitation ullamco laboris nisi ut aliquip ex ea commodo consequat.</p>
      <p class="paragraph">Excepteur sint occaecat cupidatat non proident, sunt in culpa qui officia deserunt mollit anim id est laborum. re et dolore magnam aliquam quaerat voluptatem.</p>
      <p class="closing">Regards</p>
    </section>
  </main>
</body>
</html>
```